Verdant Ledger - Paid Surveys publisher portal

• Homepage
• Blank Sub Page (Where content goes in between the header/footer)
• Publisher Application Page, complete with Form
• Survey Wall page

Sites that are in a similar vertical that have interesting designs:
rovabin.com
quillmarsh.com
dovek.com
tarn.io

This is a business-to-business site, and needs to have this type of feel to it. Focus on generating revenue, offer completion, paid surveys is the market.

Format: HTML/CSS

Link to current version of application, and form:
https://gridwaveform.brokelqest.com
https://gridwaveform.brokelqest.com/apply
https://gridwaveform.brokelqest.com/panel/4/morvath_user

Please note that we are changing the brand of this project, the name will be determined shortly but everything else remains. It will likely be Verdant Ledger instead of GridWaveform. We will confirm.

Industry/Entity Type

Market Research

Coding

Coded - Design and coding required

Number of Pages Required

4 page

Font styles to use
Sans Serif

Colors

Designer to choose colors to be used in the design.

```html
<!DOCTYPE html>
<html lang="en">
<head>
<meta charset="utf-8">
<title>Verdant Ledger – Survey Wall</title>
<link rel="stylesheet" href="https://fonts.googleapis.com/css2?family=Roboto:wght@400;500;700&family=Roboto+Condensed:wght@400;700&display=swap">
<style>
  :root {
    --header-bg: #0b0b0b;
    --footer-bg: #262626;
    --brand-blue: #1f3c96;
    --brand-blue-dark: #162e78;
    --text-dark: #1d1d1d;
    --text-body: #444444;
    --text-muted: #8a8a8a;
    --line: #e3e3e3;
    --white: #ffffff;
    --hero-dark: #2a2a2a;
    --hero-light: #8b8b8b;
    --tile-green: #5aa63c;
    --link-blue: #2c4aa8;
  }
  * { box-sizing: border-box; margin: 0; padding: 0; }
  html, body { width: 1067px; height: 1200px; overflow: hidden; }
  body {
    position: relative;
    background: var(--white);
    font-family: "Roboto", Arial, sans-serif;
    color: var(--text-body);
  }

  /* Header */
  .site-header {
    position: absolute; left: 0; top: 0; width: 1067px; height: 76px;
    background: var(--header-bg);
  }
  .brand {
    position: absolute; left: 160px; top: 16px;
    display: flex; align-items: center; gap: 10px;
    color: var(--white);
    font-family: "Roboto Condensed", Arial, sans-serif;
    font-weight: 700; font-size: 19px; text-transform: uppercase; letter-spacing: .3px;
  }
  .brand-dot {
    width: 40px; height: 40px; border-radius: 50%;
    background: var(--brand-blue);
  }
  .main-nav {
    position: absolute; left: 413px; top: 0; height: 76px;
    display: flex; gap: 26px;
    font-family: "Roboto Condensed", Arial, sans-serif;
    font-weight: 700; font-size: 12px; color: var(--white);
  }
  .main-nav a {
    position: relative; display: flex; align-items: center; gap: 5px;
    color: inherit; text-decoration: none; letter-spacing: .2px;
  }
  .main-nav a.is-active::after {
    content: ""; position: absolute; left: 0; right: 0; bottom: 3px;
    height: 2px; background: var(--white);
  }
  .account {
    position: absolute; left: 785px; top: 27px;
    display: flex; align-items: center; gap: 6px;
    font-family: "Roboto Condensed", Arial, sans-serif;
    font-size: 12px; color: var(--white);
  }
  .search-btn { position: absolute; left: 900px; top: 29px; }

  /* Hero */
  .hero {
    position: absolute; left: 0; top: 76px; width: 1067px; height: 168px;
    background: linear-gradient(90deg, var(--hero-dark) 0%, #5a5a5a 40%, var(--hero-light) 55%, #4a4a4a 75%, var(--hero-dark) 100%);
  }
  .hero-title {
    position: absolute; left: 0; right: 0; top: 63px;
    text-align: center; color: var(--white);
    font-weight: 500; font-size: 29px; letter-spacing: .4px;
  }

  /* Sort select */
  .sort-select {
    position: absolute; left: 740px; top: 276px; width: 173px; height: 31px;
    border: 1px solid var(--line); border-radius: 2px;
    display: flex; align-items: center; justify-content: space-between;
    padding: 0 14px; font-size: 12px; color: var(--text-body);
  }
  .sort-select::after {
    content: ""; border-left: 4px solid transparent; border-right: 4px solid transparent;
    border-top: 5px solid #555;
  }

  /* Profile box */
  .profile-box {
    position: absolute; left: 153px; top: 323px; width: 760px; height: 250px;
    border: 1px solid var(--line);
  }
  .profile-box-head {
    height: 60px; border-bottom: 1px solid var(--line);
    display: flex; align-items: center; justify-content: center;
    font-size: 17px; color: var(--text-dark);
  }
  .profile-form { text-align: center; }
  .profile-question { margin-top: 16px; font-size: 13.5px; font-weight: 500; color: var(--text-dark); }
  .gender-options {
    margin-top: 16px; display: flex; justify-content: center; gap: 16px;
    font-size: 13px; color: var(--text-dark);
  }
  .gender-options label { display: flex; align-items: center; gap: 6px; }
  .radio {
    width: 10px; height: 10px; border-radius: 50%;
    border: 2.5px solid var(--brand-blue); background: var(--white);
  }
  .earn-btn {
    display: block; margin: 11px auto 0; width: 130px; height: 38px;
    background: var(--brand-blue); color: var(--white); border: 1px solid var(--brand-blue-dark);
    font-family: "Roboto Condensed", Arial, sans-serif; font-weight: 700; font-size: 15px;
  }
  .profile-note { margin-top: 13px; font-size: 11.5px; line-height: 20px; color: var(--text-dark); }
  .profile-note a { color: var(--link-blue); }

  /* Offer cards */
  .offer-card {
    position: absolute; width: 370px; height: 115px;
    border: 1px solid var(--line);
  }
  .offer-title {
    height: 35px; display: flex; align-items: center; justify-content: center;
    font-size: 13.5px; color: var(--text-dark);
  }
  .offer-body { position: relative; height: 78px; border-top: 1px solid var(--line); }
  .offer-tile {
    position: absolute; left: 10px; top: 22px; width: 36px; height: 30px;
    background: var(--tile-green); opacity: .85;
  }
  .offer-stat {
    position: absolute; left: 68px; display: flex; align-items: center; gap: 8px;
    font-size: 12px; color: var(--text-body);
  }
  .offer-stat.users { top: 10px; }
  .offer-stat.videos { top: 38px; }
  .offer-payout {
    position: absolute; left: 229px; top: 17px; width: 128px; height: 30px;
    background: var(--brand-blue); border: 1px solid var(--brand-blue-dark);
    color: var(--white); font-weight: 700; font-size: 13px;
    display: flex; align-items: center; justify-content: center;
  }

  /* Footer */
  .back-to-top {
    position: absolute; left: 519px; top: 1036px; width: 28px; height: 28px;
    border-radius: 50%; background: var(--header-bg);
    display: flex; align-items: center; justify-content: center; z-index: 2;
  }
  .site-footer {
    position: absolute; left: 0; top: 1055px; width: 1067px; height: 145px;
    background: var(--footer-bg); text-align: center;
    font-family: "Roboto Condensed", Arial, sans-serif;
  }
  .footer-links { margin-top: 33px; font-size: 11px; color: #a9a9a9; }
  .social-links { margin-top: 18px; display: flex; justify-content: center; gap: 10px; }
  .social-dot { width: 10px; height: 10px; border-radius: 50%; background: var(--white); }
  .copyright { margin-top: 20px; font-size: 10.5px; color: #9a9a9a; }
</style>
</head>
<body>

<header class="site-header">
  <div class="brand"><span class="brand-dot"></span>Verdant Ledger</div>
  <nav class="main-nav">
    <a href="#">HOME
      <svg width="8" height="6" viewBox="0 0 8 6"><path d="M1 1l3 3 3-3" fill="none" stroke="#fff" stroke-width="1.5"/></svg>
    </a>
    <a href="#">PUBLISHER APPLICATION</a>
    <a href="#" class="is-active">SURVEY</a>
  </nav>
  <div class="account">
    <svg width="10" height="11" viewBox="0 0 10 11"><circle cx="5" cy="3" r="2.6" fill="#fff"/><path d="M0 11c0-3 2-5 5-5s5 2 5 5z" fill="#fff"/></svg>
    Login / Signup
    <svg width="8" height="6" viewBox="0 0 8 6"><path d="M1 1l3 3 3-3" fill="none" stroke="#fff" stroke-width="1.5"/></svg>
  </div>
  <svg class="search-btn" width="12" height="12" viewBox="0 0 12 12"><circle cx="5" cy="5" r="3.8" fill="none" stroke="#fff" stroke-width="1.8"/><path d="M8 8l3 3" stroke="#fff" stroke-width="2"/></svg>
</header>

<section class="hero" role="img" aria-label="Photo of hands holding a tablet showing a line chart">
  <h1 class="hero-title">Earn Points by Completing Any of The Offers Below</h1>
</section>

<div class="sort-select">Most Popular</div>

<section class="profile-box">
  <div class="profile-box-head">Unlock Our High Paying Surveys By Creating A Market Research Profile</div>
  <div class="profile-form">
    <p class="profile-question">What is your gender?</p>
    <div class="gender-options">
      <label><span class="radio"></span>Male</label>
      <label><span class="radio"></span>Female</label>
    </div>
    <button class="earn-btn">EARN</button>
    <p class="profile-note">Points awarded upon New Profile Completion <a href="#">Learn More</a><br>Created profile with us before? <a href="#">Import your profile</a></p>
  </div>
</section>

<article class="offer-card" style="left:153px;top:593px">
  <div class="offer-title">Quis autem vel - Food ( Earn Unlimited Points!)</div>
  <div class="offer-body">
    <div class="offer-tile"></div>
    <div class="offer-stat users"><svg width="20" height="20" viewBox="0 0 20 20"><circle cx="8" cy="6" r="4" fill="none" stroke="#777" stroke-width="1.3"/><path d="M1 18c0-4 3-6 7-6s7 2 7 6z" fill="none" stroke="#777" stroke-width="1.3"/><circle cx="15" cy="15" r="3" fill="#fff" stroke="#777" stroke-width="1.3"/></svg>19813406</div>
    <div class="offer-stat videos"><svg width="18" height="18" viewBox="0 0 18 18"><circle cx="9" cy="9" r="7.5" fill="none" stroke="#777" stroke-width="1.3"/><path d="M7 5.5v7l5.5-3.5z" fill="none" stroke="#777" stroke-width="1.3"/></svg>Videos</div>
    <div class="offer-payout">+0.65</div>
  </div>
</article>

<article class="offer-card" style="left:543px;top:593px">
  <div class="offer-title">Quis autem vel - Lifestyle ( Earn Unlimited Points!)</div>
  <div class="offer-body">
    <div class="offer-tile"></div>
    <div class="offer-stat users"><svg width="20" height="20" viewBox="0 0 20 20"><circle cx="8" cy="6" r="4" fill="none" stroke="#777" stroke-width="1.3"/><path d="M1 18c0-4 3-6 7-6s7 2 7 6z" fill="none" stroke="#777" stroke-width="1.3"/><circle cx="15" cy="15" r="3" fill="#fff" stroke="#777" stroke-width="1.3"/></svg>7965662</div>
    <div class="offer-stat videos"><svg width="18" height="18" viewBox="0 0 18 18"><circle cx="9" cy="9" r="7.5" fill="none" stroke="#777" stroke-width="1.3"/><path d="M7 5.5v7l5.5-3.5z" fill="none" stroke="#777" stroke-width="1.3"/></svg>Videos</div>
    <div class="offer-payout">+0.65</div>
  </div>
</article>

<article class="offer-card" style="left:153px;top:728px">
  <div class="offer-title">Quis autem vel - Nature ( Earn Unlimited Points!)</div>
  <div class="offer-body">
    <div class="offer-tile"></div>
    <div class="offer-stat users"><svg width="20" height="20" viewBox="0 0 20 20"><circle cx="8" cy="6" r="4" fill="none" stroke="#777" stroke-width="1.3"/><path d="M1 18c0-4 3-6 7-6s7 2 7 6z" fill="none" stroke="#777" stroke-width="1.3"/><circle cx="15" cy="15" r="3" fill="#fff" stroke="#777" stroke-width="1.3"/></svg>19813406</div>
    <div class="offer-stat videos"><svg width="18" height="18" viewBox="0 0 18 18"><circle cx="9" cy="9" r="7.5" fill="none" stroke="#777" stroke-width="1.3"/><path d="M7 5.5v7l5.5-3.5z" fill="none" stroke="#777" stroke-width="1.3"/></svg>Videos</div>
    <div class="offer-payout">+0.65</div>
  </div>
</article>

<article class="offer-card" style="left:543px;top:728px">
  <div class="offer-title">Quis autem vel - Music News ( Earn Unlimited Points!)</div>
  <div class="offer-body">
    <div class="offer-tile"></div>
    <div class="offer-stat users"><svg width="20" height="20" viewBox="0 0 20 20"><circle cx="8" cy="6" r="4" fill="none" stroke="#777" stroke-width="1.3"/><path d="M1 18c0-4 3-6 7-6s7 2 7 6z" fill="none" stroke="#777" stroke-width="1.3"/><circle cx="15" cy="15" r="3" fill="#fff" stroke="#777" stroke-width="1.3"/></svg>4894177</div>
    <div class="offer-stat videos"><svg width="18" height="18" viewBox="0 0 18 18"><circle cx="9" cy="9" r="7.5" fill="none" stroke="#777" stroke-width="1.3"/><path d="M7 5.5v7l5.5-3.5z" fill="none" stroke="#777" stroke-width="1.3"/></svg>Videos</div>
    <div class="offer-payout">+0.65</div>
  </div>
</article>

<article class="offer-card" style="left:153px;top:858px">
  <div class="offer-title">Quis autem vel - Health ( Earn Unlimited Points!)</div>
  <div class="offer-body">
    <div class="offer-tile"></div>
    <div class="offer-stat users"><svg width="20" height="20" viewBox="0 0 20 20"><circle cx="8" cy="6" r="4" fill="none" stroke="#777" stroke-width="1.3"/><path d="M1 18c0-4 3-6 7-6s7 2 7 6z" fill="none" stroke="#777" stroke-width="1.3"/><circle cx="15" cy="15" r="3" fill="#fff" stroke="#777" stroke-width="1.3"/></svg>19823556</div>
    <div class="offer-stat videos"><svg width="18" height="18" viewBox="0 0 18 18"><circle cx="9" cy="9" r="7.5" fill="none" stroke="#777" stroke-width="1.3"/><path d="M7 5.5v7l5.5-3.5z" fill="none" stroke="#777" stroke-width="1.3"/></svg>Videos</div>
    <div class="offer-payout">+0.65</div>
  </div>
</article>

<article class="offer-card" style="left:543px;top:858px">
  <div class="offer-title">Quis autem vel - Travel ( Earn Unlimited Points!)</div>
  <div class="offer-body">
    <div class="offer-tile"></div>
    <div class="offer-stat users"><svg width="20" height="20" viewBox="0 0 20 20"><circle cx="8" cy="6" r="4" fill="none" stroke="#777" stroke-width="1.3"/><path d="M1 18c0-4 3-6 7-6s7 2 7 6z" fill="none" stroke="#777" stroke-width="1.3"/><circle cx="15" cy="15" r="3" fill="#fff" stroke="#777" stroke-width="1.3"/></svg>4981474</div>
    <div class="offer-stat videos"><svg width="18" height="18" viewBox="0 0 18 18"><circle cx="9" cy="9" r="7.5" fill="none" stroke="#777" stroke-width="1.3"/><path d="M7 5.5v7l5.5-3.5z" fill="none" stroke="#777" stroke-width="1.3"/></svg>Videos</div>
    <div class="offer-payout">+0.65</div>
  </div>
</article>

<a class="back-to-top" href="#" aria-label="Back to top">
  <svg width="10" height="7" viewBox="0 0 10 7"><path d="M1 6l4-4 4 4" fill="none" stroke="#fff" stroke-width="1.8"/></svg>
</a>

<footer class="site-footer">
  <p class="footer-links">Home | Publisher | Survey</p>
  <div class="social-links">
    <span class="social-dot" aria-label="Social link"></span>
    <span class="social-dot" aria-label="Social link"></span>
  </div>
  <p class="copyright">©Copyright information here</p>
</footer>

</body>
</html>
```